Poster for a online company that buys your stuff

SwapKestrel offers a website which customers can get a instant offer for stuff their looking to sell. They then Courier the items in to us and they get paid the same day it arrives
We're looking for an eye catching design which portrays our hassle free process
We'll need your help to come up with a slogan/catch phrase and our easy 1,2,3 process so customers can see the poster and instantly have a clear understanding of what we do
1. Get an instant offer on our website
2. Send your item(s) to us
3.Get paid within 24 Hours
Industry/Entity Type
It Company
Look and feel
Each slider illustrates characteristics of the customer's brand and the style your logo design should communicate.

```html
<!DOCTYPE html>
<html lang="en">
<head>
<meta charset="utf-8">
<title>SwapKestrel Poster</title>
<link rel="stylesheet" href="https://fonts.googleapis.com/css2?family=Arimo:wght@400;700&display=swap">
<style>
  :root {
    --backdrop: #6b6b6b;
    --paper-top: #eceeee;
    --paper: #ffffff;
    --ink: #222222;
    --ink-dark: #2b2b2b;
    --green: #1f9a2e;
    --green-deep: #0b6b1a;
    --green-mid: #43a84a;
    --green-light: #c6df8f;
    --lime: #8cc41e;
    --icon-bg: #333030;
  }
  * { box-sizing: border-box; margin: 0; padding: 0; }
  html, body { width: 900px; height: 1200px; overflow: hidden; }
  body { background: var(--backdrop); font-family: "Arimo", Arial, sans-serif; position: relative; }

  .poster {
    position: absolute; left: 146px; top: 150px;
    width: 628px; height: 887px;
    background: var(--paper-top);
    overflow: hidden;
  }
  .mascot {
    position: absolute; left: 174px; top: 25px; width: 310px; height: 272px;
    border-radius: 50% 50% 40% 40%;
    background: radial-gradient(ellipse at 50% 45%, #f2a81f 0%, #8cc41e 45%, rgba(236,238,238,0) 72%);
  }
  .brand-name {
    position: absolute; left: 0; right: 0; top: 290px;
    text-align: center; font-weight: 700; font-size: 52px;
    color: var(--ink-dark); letter-spacing: -1px;
  }
  .swoosh { position: absolute; left: 0; top: 340px; width: 628px; height: 547px; }

  .headline { position: absolute; left: 0; right: 0; text-align: center; }
  .headline-lead { top: 463px; font-size: 30px; color: var(--ink); }
  .headline-main { top: 494px; font-size: 86px; color: var(--green); letter-spacing: 9px; line-height: 1; }
  .headline-sub { top: 580px; font-size: 35px; font-weight: 700; color: var(--green); }

  .steps { position: absolute; left: 0; top: 600px; width: 628px; height: 220px; }
  .step-caption {
    position: absolute; top: 777px; width: 200px; text-align: center;
    font-size: 15px; line-height: 18px; color: var(--ink);
  }
  .step-number { position: absolute; top: 670px; font-size: 22px; color: var(--ink); }

  .call-bar { position: absolute; left: 0; top: 828px; width: 628px; height: 59px; }
  .call-label {
    position: absolute; left: 38px; top: 830px; font-size: 42px; color: var(--paper);
  }
  .call-number {
    position: absolute; left: 253px; top: 830px; font-size: 44px; font-weight: 700; color: var(--ink);
  }
</style>
</head>
<body>
  <main class="poster">
    <div class="mascot" role="img" aria-label="Illustrated courier mascot carrying a parcel and giving a thumbs up"></div>
    <div class="brand-name">SwapKestrel</div>

    <svg class="swoosh" viewBox="0 0 628 547" aria-hidden="true">
      <path d="M0 110 Q300 -65 628 80 L628 547 L0 547 Z" fill="var(--green-light)"/>
      <path d="M0 130 Q300 -55 628 100 L628 547 L0 547 Z" fill="var(--green-mid)"/>
      <path d="M0 150 Q310 -35 628 120 L628 547 L0 547 Z" fill="var(--green-deep)"/>
      <path d="M0 165 Q310 -28 628 150 L628 547 L0 547 Z" fill="var(--green)"/>
      <path d="M0 172 Q310 -23 628 175 L628 547 L0 547 Z" fill="var(--green-mid)"/>
      <path d="M0 175 Q310 -8 628 200 L628 547 L0 547 Z" fill="var(--paper)"/>
    </svg>

    <div class="headline headline-lead">SELL YOUR PRODUCTS</div>
    <div class="headline headline-main">EASILY</div>
    <div class="headline headline-sub">IN 3 SIMPLE STEPS</div>

    <svg class="steps" viewBox="0 0 628 220" aria-hidden="true">
      <g stroke="var(--green)" stroke-width="1.2" fill="none">
        <path d="M320 22 V40 M117 40 H523 M117 40 V66 M320 40 V66 M523 40 V66"/>
      </g>
      <g>
        <circle cx="123" cy="117" r="51" fill="var(--lime)"/>
        <circle cx="123" cy="117" r="43" fill="var(--icon-bg)"/>
        <circle cx="324" cy="117" r="51" fill="var(--lime)"/>
        <circle cx="324" cy="117" r="43" fill="var(--icon-bg)"/>
        <circle cx="519" cy="117" r="51" fill="var(--lime)"/>
        <circle cx="519" cy="117" r="43" fill="var(--icon-bg)"/>
      </g>
      <g class="icon-globe" stroke="#fff" stroke-width="1.6" fill="none">
        <circle cx="123" cy="117" r="24"/>
        <ellipse cx="123" cy="117" rx="10" ry="24"/>
        <path d="M123 93 V141 M99 117 H147 M103 105 H143 M103 129 H143"/>
      </g>
      <g class="icon-trolley" stroke="#fff" stroke-width="2" fill="none">
        <path d="M302 96 H308 V134 H346"/>
        <rect x="314" y="106" width="26" height="24"/>
        <path d="M322 106 V130 M332 106 V130"/>
        <circle cx="314" cy="139" r="3"/>
        <circle cx="340" cy="139" r="3"/>
      </g>
      <g class="icon-payday">
        <path d="M503 104 A25 25 0 1 1 499 134" stroke="#fff" stroke-width="3" fill="none"/>
        <path d="M496 98 L508 100 L502 110 Z" fill="#fff"/>
        <circle cx="527" cy="101" r="9" stroke="#fff" stroke-width="1.6" fill="none"/>
        <text x="527" y="106" text-anchor="middle" font-family="Arimo, Arial, sans-serif" font-size="13" fill="#fff">P</text>
        <text x="511" y="133" text-anchor="middle" font-family="Arimo, Arial, sans-serif" font-weight="700" font-size="17" fill="#fff">24h</text>
      </g>
    </svg>

    <span class="step-number" style="left:61px">1</span>
    <span class="step-number" style="left:255px">2</span>
    <span class="step-number" style="left:450px">3</span>
    <p class="step-caption" style="left:23px">Get an instant<br>offer on our website</p>
    <p class="step-caption" style="left:224px">Send your<br>item(s) to us</p>
    <p class="step-caption" style="left:420px">Get paid<br>within 24 Hours</p>

    <svg class="call-bar" viewBox="0 0 628 59" aria-hidden="true">
      <path d="M0 0 H200 L235 50 H0 Z" fill="var(--green)"/>
      <rect x="0" y="50" width="628" height="9" fill="var(--green)"/>
    </svg>
    <div class="call-label">Call us:</div>
    <div class="call-number">077- 4218- 6032</div>
  </main>
</body>
</html>
```